Venture Capital Investment Firm

We are looking to overhaul our existing website (substantially), with only using the same logos (which we can provide).
We are an investment firm that focuses on making loans to late stage technology companies. Our site should ultimately look like other venture capital firms, and look modern and fresh. We have an existing website www.norvellhub.com which this will be replacing, although we will be using a lot of the existing written content, and potentially the numbers of pages we will need, we are not wed to anything else. Please feel free to shoot any questions at any time and thank you in advance for your help!
Websites we like as examples:
https://www.tesmarkfund.com/
https://www.brindlewoodpartners.com/
Target Market(s)
Potential investors who will invest in our firm, as well as potentially companies that are looking to borrow money from us.
Coding
Coded - Design and coding required
Number of Pages Required
5+ page
Colors
Designer to choose colors to be used in the design.
Look and feel

```html
<!DOCTYPE html>
<html lang="en">
<head>
<meta charset="utf-8">
<title>Norvell Hub Investment Partners</title>
<link href="https://fonts.googleapis.com/css2?family=Cinzel:wght@700&family=Lato:wght@400;700&display=swap" rel="stylesheet">
<style>
:root{
  --navy:#0b0b3b;
  --ink:#222233;
  --muted:#444;
  --strategy:#3d3b5e;
  --frame:#5b5979;
  --news-bg:#f5f5f5;
  --contact-bg:#d8d5f8;
  --footer:#2b2b2b;
  --white:#fff;
  --rule:#b9b9c4;
}
*{box-sizing:border-box;margin:0;padding:0}
html,body{width:1200px;height:2954px;overflow:hidden}
body{font-family:'Lato',sans-serif;color:var(--ink);background:var(--white)}
.wrap{width:976px;margin:0 auto;position:relative}
.site-header{height:98px;display:flex;align-items:center}
.site-header .wrap{display:flex;justify-content:space-between;align-items:center}
.brand{display:flex;align-items:center;gap:14px}
.brand-dot{width:44px;height:44px;border-radius:50%;background:var(--navy)}
.brand-name{font-family:'Cinzel',serif;font-weight:700;font-size:30px;color:var(--navy);line-height:1}
.nav{display:flex;gap:34px;font-size:14px;color:var(--ink)}
.nav a{color:inherit;text-decoration:none;padding-bottom:8px}
.nav a.active{font-weight:700;color:var(--navy);border-bottom:3px solid var(--navy)}
.hero{height:600px;background:linear-gradient(180deg,#5d6488 0%,#3e4470 55%,#2a2f55 100%);position:relative;text-align:center;color:var(--white)}
.hero h1{font-family:'Cinzel',serif;font-size:53px;padding-top:173px;letter-spacing:1px;line-height:1}
.hero p{font-size:20px;line-height:28px;margin-top:14px;text-transform:uppercase}
.btn{display:inline-block;font-size:17px;text-decoration:none;text-align:center}
.btn-ghost{border:2px solid var(--white);color:var(--white);width:156px;height:52px;line-height:48px;margin-top:30px}
.dots{position:absolute;left:0;right:0;bottom:36px;display:flex;justify-content:center;gap:4px}
.dots span{width:14px;height:14px;border-radius:50%;border:2px solid var(--white)}
.dots span.on{background:var(--white)}
.section-title{display:flex;justify-content:center;align-items:center;gap:12px;font-family:'Cinzel',serif;font-size:38px;color:var(--navy)}
.section-title::before,.section-title::after{content:"";width:106px;height:2px;background:var(--rule)}
.welcome{height:465px;text-align:center;padding-top:54px}
.welcome p{font-size:13px;line-height:28px;color:var(--muted);margin-top:16px}
.welcome .section-title+p{margin-top:18px}
.btn-solid{background:var(--navy);color:var(--white);width:155px;height:52px;line-height:52px;margin-top:38px}
.strategy{height:636px;background:var(--strategy);padding-top:68px;color:var(--white)}
.strategy .section-title{color:var(--white)}
.strategy .section-title::before,.strategy .section-title::after{background:#6b6a8a}
.strategy-body{display:flex;gap:42px;margin-top:50px}
.strategy-photo{width:552px;height:358px;border:8px solid var(--frame);background:linear-gradient(135deg,#2d3650,#9fb2c9 55%,#e4ebf2)}
.strategy-text{width:390px;font-size:13.5px;line-height:25px}
.strategy-text p+p{margin-top:14px}
.btn-light{background:var(--white);color:var(--strategy);width:144px;height:50px;line-height:50px;margin-top:28px}
.news{height:573px;background:var(--news-bg);padding-top:64px;position:relative}
.news-grid{display:flex;gap:35px;margin-top:42px}
.card{width:302px}
.card-photo{height:175px;position:relative}
.date{position:absolute;left:0;bottom:0;background:var(--navy);color:var(--white);font-size:10px;font-weight:700;padding:0 12px;height:38px;line-height:38px;width:113px}
.card h3{font-size:18px;line-height:22px;color:var(--navy);margin-top:16px}
.card p{font-size:12.5px;line-height:20px;color:var(--muted);margin-top:10px;padding-left:2px}
.card a{display:block;font-size:15px;font-weight:700;color:var(--navy);text-decoration:none;margin-top:24px;padding-left:2px}
.arrow{position:absolute;top:218px}
.arrow-left{left:-70px}.arrow-right{right:-70px}
.contact{height:520px;background:var(--contact-bg);padding-top:64px}
.contact-body{display:flex;justify-content:space-between;margin-top:50px}
.info{width:330px;font-size:16px;line-height:23px}
.info-row{display:flex;gap:10px}
.info-row+.info-row{margin-top:38px;align-items:center}
.socials{display:flex;gap:6px;margin-top:42px}
.socials span{width:38px;height:38px;border-radius:50%;background:var(--navy)}
.form{width:591px;display:grid;grid-template-columns:1fr 1fr;gap:20px 8px}
.field{background:var(--white);border:1px solid #c8c6e0;height:40px;font-size:13px;color:#666;padding:11px 13px}
.field.full{grid-column:1/3}
.field.msg{height:92px}
.submit{grid-column:1/2;width:146px;height:48px;background:var(--navy);color:var(--white);font-size:16px;line-height:48px;text-align:center}
.site-footer{height:62px;background:var(--footer);color:#ddd;font-size:12px;display:flex;align-items:center;justify-content:center;position:relative}
.site-footer .code{position:absolute;right:40px}
</style>
</head>
<body>
<header class="site-header">
  <div class="wrap">
    <div class="brand"><span class="brand-dot"></span><span class="brand-name">Norvell Hub</span></div>
    <nav class="nav">
      <a class="active" href="#">HOME</a><a href="#">ABOUT US</a><a href="#">STRATEGY</a><a href="#">TEAM</a><a href="#">NEWS</a><a href="#">INVESTORS</a><a href="#">CONTACT</a>
    </nav>
  </div>
</header>

<section class="hero" role="img" aria-label="Businessman standing by office window overlooking city skyline">
  <h1>NORVELL HUB INVESTMETN PARTNER</h1>
  <p>We are a global structured credit investment firm focused on the<br>healthcare and technology industries</p>
  <a class="btn btn-ghost" href="#">LEARN MORE</a>
  <div class="dots"><span class="on"></span><span></span><span></span><span></span></div>
</section>

<section class="welcome">
  <div class="wrap">
    <h2 class="section-title">WELCOME TO NORVELL HUB</h2>
    <p>Norvell Hub is a private investment firm unique in its dual focus on life science and technology credit opportunities.&nbsp; Our ambidextrous approach to investing reflects a broad recognition and appreciation for the critical role intellectual property plays in the successful commercialization of products.&nbsp; We apply our extensive industry expertise to assess the revenue visibility created by these assets and offer a range of creative financing solutions.</p>
    <p>A pioneer in providing life science structured credit beginning in 2004, the Norvell Hub team was the first to introduce flexible structured credit to the technology sector in 2014.&nbsp; Our team was also early to recognize the potential of "non-core" assets beyond drug royalties, acquiring over $300M of branded generics offering predictable cash flows from large pharmaceutical firms and partnering with entrepreneurial teams to successfully manage these brands.</p>
    <a class="btn btn-solid" href="#">READ MORE</a>
  </div>
</section>

<section class="strategy">
  <div class="wrap">
    <h2 class="section-title">OUR STRATEGY</h2>
    <div class="strategy-body">
      <div class="strategy-photo" role="img" aria-label="Business people reviewing charts on a tablet at a meeting table"></div>
      <div class="strategy-text">
        <p>Norvell Hub's proven strategy focuses on identifying opportunities where demonstrated commercial success has established underlying asset or enterprise value prior to our investment.&nbsp; We tailor our financing solutions to each situation with the goal of preserving our partners' ownership interests, aligning incentives, and providing operating flexibility to build businesses of value.</p>
        <p>Our approach enables us to work flexibly to meet the needs of companies, investors, and entrepreneurs we partner with through a wide array of transaction structures:</p>
        <a class="btn btn-light" href="#">LEARN MORE</a>
      </div>
    </div>
  </div>
</section>

<section class="news">
  <div class="wrap">
    <h2 class="section-title">NORVELL HUB NEWS</h2>
    <div class="news-grid">
      <article class="card">
        <div class="card-photo" role="img" aria-label="Two businessmen shaking hands" style="background:linear-gradient(135deg,#3a3f4a,#b9c3cf 60%,#e8ecf0)"><span class="date">APRIL 30, 2018</span></div>
        <h3>Norvell Hub completes structured debt investment in Loomdrift</h3>
        <p>Norvell Hub Investment Partners (“Norvell Hub”) announced today that it has completed a structured debt investment.</p>
        <a href="#">READ MORE</a>
      </article>
      <article class="card">
        <div class="card-photo" role="img" aria-label="Hand placing a block on a stack of wooden blocks and coins" style="background:linear-gradient(135deg,#8fa0b8,#5b6678 50%,#1d2230)"><span class="date">OCTOBER 19, 2016</span></div>
        <h3>Norvell Hub completes $22,000,000 structured debt investment</h3>
        <p>Norvell Hub Investment Partners (“Norvell Hub”) announced today that it has completed a $22,000,000 structured debt investment.</p>
        <a href="#">READ MORE</a>
      </article>
      <article class="card">
        <div class="card-photo" role="img" aria-label="Team reviewing printed charts beside a laptop" style="background:linear-gradient(135deg,#2e3b55,#8e9fb8 50%,#d7dde6)"><span class="date">APRIL 4, 2016</span></div>
        <h3>Corvane Semiconductor acquired by Altrion for $55,000,000</h3>
        <p>Altrion Optics, Inc., a leading supplier of advanced semiconductor communications components for use in Cloud connectivity,data centers.</p>
        <a href="#">READ MORE</a>
      </article>
    </div>
    <svg class="arrow arrow-left" width="26" height="48" viewBox="0 0 26 48"><polyline points="24,2 2,24 24,46" fill="none" stroke="#999" stroke-width="2"/></svg>
    <svg class="arrow arrow-right" width="26" height="48" viewBox="0 0 26 48"><polyline points="2,2 24,24 2,46" fill="none" stroke="#999" stroke-width="2"/></svg>
  </div>
</section>

<section class="contact">
  <div class="wrap">
    <h2 class="section-title">CONTAC US</h2>
    <div class="contact-body">
      <div class="info">
        <div class="info-row">
          <svg width="14" height="20" viewBox="0 0 14 20" style="margin-top:4px"><path d="M7 0C3 0 0 3 0 7c0 5 7 13 7 13s7-8 7-13c0-4-3-7-7-7z" fill="var(--navy)"/><circle cx="7" cy="7" r="2.6" fill="var(--contact-bg)"/></svg>
          <div>SAN FRANCISCO<br>1450 Harlow Street #310<br>San Francisco, CA&nbsp; 94107</div>
        </div>
        <div class="info-row">
          <svg width="18" height="13" viewBox="0 0 18 13"><rect width="18" height="13" rx="1" fill="var(--navy)"/><polyline points="1,1 9,7 17,1" fill="none" stroke="var(--contact-bg)" stroke-width="1.5"/></svg>
          <div>inquiries@norvellhub.com</div>
        </div>
        <div class="socials"><span aria-label="Social profile"></span><span aria-label="Social profile"></span></div>
      </div>
      <form class="form">
        <div class="field">Your name</div>
        <div class="field">Phone number</div>
        <div class="field full">Email</div>
        <div class="field full msg">Your message</div>
        <div class="submit">SUBMIT NOW</div>
      </form>
    </div>
  </div>
</section>

<footer class="site-footer">
  <span>Copyrights © 2019 Norvell Hub Investment Partners LLC.&nbsp; All rights reserved.</span>
  <span class="code">C16</span>
</footer>
</body>
</html>
```